Northway Value Bureau (Account) WP Design

We need an Account (Profile) Wordpress design to add to nvb.co.uk.

The design should be based on https://nvb.co.uk/about/. The look and feel of the menu on the left.

The logic, after login the header menu will add another page:

Before Login:
Home / About / Trading / Support /

After Login
Home / About / Trading / Support / Account (Demo) - Logout

When you click on the / Account /

"Account Profile" page is loaded where you can change the settings etc.

"Account Profile" menu on the left should look the same as in / About / (https://nvb.co.uk/about/)

We need the following sub-pages under "Account Profile"

- Profile
- Transfers
- Reports
- Security
- API Key
- Affiliates

Now looking into each page:
-
- Profile (Should be split into individual or business) a user can choose whether how he want to run his account:

[Individual]

Personal Details
First Name:
Middle Name:
Family Name:
Citizenship:
Gender:
DOB:

[Attach File] (Government Issues ID, Passport, Driving License) - Verify

Contact Information
Phone: +44 207 555 0143 - Verify
E-Mail: sample@mailbox.example - Verify

Residential Address
Address line 1:
Address line 2:
Address line 3:
City:
Postcode:
Country:

[Attach File] (Utility Bill or Bank Statement) - Verify

[Business]

Company Name:
Registration Number:

Registered Address
Address line 1:
Address line 2:
Address line 3:
City:
Postcode:
Country:

[Attach File] (Certificate of Incorporation) - Verify
[Attach File] (Memorandum & Articles of Association)
[Attach File] (Shareholder Register)

Company Contact Information
Website:

-

- Transfers (Where a user can link a bank account to deposit or withdraw funds from the account)

Transfers

Add a bank account:

Please select the country where beneficiary’s bank is domicile: [Please select]
Please select the currency you wish to make transfers in: [Please select]

Full beneficiary name:
Full beneficiary address:
Beneficiary bank name:
Beneficiary bank address:
Beneficiary Bank Identification Code (BIC)/Routing Code:
Beneficiary IBAN number/account number:

[SAVE]

Deposti funds to NVB Bank Account
Amount of currency to be received e.g. 2345.67 [Please select: USD, EUR, GBP] :
Full beneficiary name: Northway Value Bureau Limited
Full beneficiary address: Kestrel Court
7-9 Fenwick Row
London, United Kingdom
Beneficiary bank name:
Beneficiary bank address:
Beneficiary Bank Identification Code (BIC)/Routing Code: XXXXXXXXXX
Beneficiary IBAN number/account number: XXXXXXXXXXXXXXXXXXXXXXXXXX

Deposit coins to NVB Coin Account
Amount of coins to be received e.g. 2345.67 [Please select: BTC, LTC]:
NVB Coin Account: XXXXXXXXXXXXXXXXXXXXXXXXXXXXX

Applicable charges (?):
[Clear] [Continue]

Withdraw funds from NVB Bank Account
Amount of currency to be sent e.g. 2345.67 [Please select: USD, EUR, GBP] :

Withdraw coins from NVB Coin Account:
Amount of coins to be sent e.g. 2345.67 [Please select: BTC, LTC]:
Please specify you coin account: XXXXXXXXXXXXXXXXXXXXXXXXXXXXX

Applicable charges (?):
[Clear] [Continue]

-

- Reports

TBC
-

- Security

Change Password
Current Password:
New Password:
Confirm New Password:

Enable / Disable : Two-factor Authentication (SMS)

-

- API Key
TBC

-
- Affiliates

Unlimited earning potential!
You'll receive up to 10% commission on all trades made through your affiliate link.

Referral Circle Scheme
Simply apply to our program from your publisher account or click the "Join Now" button below.

Corvalent.com - Join Now

```html
<!DOCTYPE html>
<html lang="en">
<head>
<meta charset="utf-8">
<title>Northway Value Bureau – Account Profile</title>
<link href="https://fonts.googleapis.com/css2?family=Arimo:wght@400;700&display=swap" rel="stylesheet">
<style>
:root{
  --backdrop:#3a3a3a;
  --paper:#ffffff;
  --brand:#0096d1;
  --brand-dark:#0a86bd;
  --ink:#222222;
  --muted:#555555;
  --rule:#bdbdbd;
  --field:#b9b9b9;
  --band:#e6e6e6;
  --button-dark:#3a3a3a;
}
*{box-sizing:border-box;margin:0;padding:0}
html,body{width:1016px;height:1200px;overflow:hidden;background:var(--backdrop);font-family:"Arimo",Arial,sans-serif;color:var(--ink)}
.stage{position:absolute;left:0;top:0;width:1200px;height:1417px;transform:scale(0.84667);transform-origin:0 0}
.sheet{position:absolute;left:66px;top:0;width:1068px;height:1383px;background:var(--paper)}
.abs{position:absolute}
/* header */
.brand-name{left:164px;top:20px;width:130px;font-size:13px;letter-spacing:2px;line-height:18px;text-transform:uppercase;color:#333}
.brand-divider{left:308px;top:12px;width:1px;height:62px;background:#999}
.brand-dot{left:322px;top:23px;width:13px;height:13px;border-radius:50%;background:var(--brand)}
.main-nav{left:320px;top:59px;font-size:11px;color:#555}
.login{top:36px;height:23px}
.login-input{border:1px solid var(--field);font-size:11px;color:#999;padding:5px 4px;width:117px}
.help{position:absolute;right:10px;top:3px;width:15px;height:15px;border:1px solid #bbb;border-radius:50%;font-size:9px;text-align:center;line-height:13px;color:#aaa}
.btn{font-size:10px;font-weight:700;color:#fff;text-align:center;line-height:23px;border-radius:2px}
/* ticker */
.ticker{left:66px;top:91px;width:1068px;height:43px;background:var(--brand)}
.tick{position:absolute;top:6px;color:#fff;padding-left:21px;height:33px;border-left:1px solid rgba(255,255,255,.45)}
.tick small{display:block;font-size:9.5px}
.tick b{font-weight:400;font-size:12.5px}
.coin{position:absolute;left:277px;top:98px;width:28px;height:28px;border:2px solid #fff;border-radius:50%}
/* title band */
.title-band{left:66px;top:134px;width:1068px;height:71px;background:var(--band);border-bottom:1px solid #d2d2d2}
.title-band h1{position:absolute;left:112px;top:20px;font-size:27px;font-weight:700;color:#111}
/* side menu */
.side-menu{left:178px;top:233px;width:193px;list-style:none}
.side-menu li{height:34px;border-bottom:1px solid #555;font-size:14.5px;line-height:32px;position:relative}
.side-menu li:last-child{border-bottom:none}
.plus{position:absolute;right:2px;top:10px;width:14px;height:14px;background:#999;color:#fff;font-size:13px;line-height:13px;text-align:center}
/* form */
.section-title{left:421px;top:242px;font-size:26px;font-weight:700;color:#555}
.radios{left:441px;top:290px;font-size:13px}
.radio{display:inline-block;width:12px;height:12px;border:1px solid #999;border-radius:50%;vertical-align:-2px;margin-right:8px;position:relative}
.radio.on::after{content:"";position:absolute;left:2px;top:2px;width:6px;height:6px;border-radius:50%;background:var(--brand)}
.group{left:454px;font-size:13px;font-weight:700}
.label{width:200px;left:345px;text-align:right;font-size:13px}
.field{left:563px;width:190px;height:26px;border:1px solid var(--field);font-size:11.5px;padding:6px 11px;color:#222}
.field.hint{color:#888}
.chev{position:absolute;right:9px;top:6px}
.verify{left:758px;width:67px;height:22px;background:var(--brand-dark);color:#fff;font-size:11px;font-weight:700;line-height:22px}
.verify span{display:inline-block;width:21px;height:22px;background:#1b6f99;text-align:center;margin-right:6px;vertical-align:top}
/* footer */
.footer{left:66px;top:1088px;width:1068px;height:295px;background:var(--brand);color:#fff}
.footer h3{position:absolute;top:37px;font-size:19px;font-weight:700}
.footer ul{position:absolute;top:71px;list-style:none;font-size:10.5px;line-height:13.3px}
.social{position:absolute;top:72px;width:25px;height:25px;border-radius:50%;background:#fff}
</style>
</head>
<body>
<div class="stage">
  <div class="sheet"></div>

  <!-- header -->
  <div class="abs brand-name">Northway Value Bureau</div>
  <div class="abs brand-divider"></div>
  <div class="abs brand-dot"></div>
  <div class="abs main-nav">Home · About · Trading · Support · Account (Demo) - Logout</div>
  <div class="abs login login-input" style="left:684px">Email<span class="help">?</span></div>
  <div class="abs login login-input" style="left:808px">Password<span class="help">?</span></div>
  <div class="abs login btn" style="left:933px;width:48px;background:var(--button-dark)">Log In</div>
  <div class="abs login btn" style="left:986px;width:49px;background:var(--brand)">Sign Up</div>

  <!-- ticker -->
  <div class="abs ticker"></div>
  <div class="coin"></div>
  <div class="tick" style="left:296px;border-left:none"><small>Current Price</small><b>$444.13</b></div>
  <div class="tick" style="left:397px"><small>Daily Change</small><b>-9.54 <span style="font-size:9px">▾2.10%</span></b></div>
  <div class="tick" style="left:509px"><small>Day's Range</small><b>$440.00 - $457.30</b></div>
  <div class="tick" style="left:658px"><small>Today's Open</small><b>$453.57</b></div>
  <div class="tick" style="left:763px"><small>24h Volume</small><b>7194 BTC</b></div>

  <div class="abs title-band"><h1>Account Profile</h1></div>

  <ul class="abs side-menu">
    <li>Profile</li>
    <li>Transfers<span class="plus">+</span></li>
    <li>Reports</li>
    <li>Security</li>
    <li>API Key</li>
    <li>Affiliates</li>
  </ul>

  <div class="abs section-title">Profile</div>
  <div class="abs radios"><span class="radio on"></span>Individual <span style="display:inline-block;width:10px"></span><span class="radio"></span>Business</div>

  <div class="abs group" style="top:331px">Personal Details</div>
  <div class="abs label" style="top:369px">First Name:</div><div class="abs field" style="top:363px"></div>
  <div class="abs label" style="top:405px">Middle Name:</div><div class="abs field" style="top:399px"></div>
  <div class="abs label" style="top:440px">Family Name:</div><div class="abs field" style="top:434px"></div>
  <div class="abs label" style="top:476px">Citizenship:</div><div class="abs field" style="top:470px"><svg class="chev" width="10" height="10"><path d="M1 3l4 4 4-4" fill="none" stroke="#555" stroke-width="1.3"/></svg></div>
  <div class="abs label" style="top:512px">Gender:</div><div class="abs field" style="top:506px">Male<svg class="chev" width="10" height="10"><path d="M1 3l4 4 4-4" fill="none" stroke="#555" stroke-width="1.3"/></svg></div>
  <div class="abs label" style="top:547px">DOB:</div><div class="abs field" style="top:541px">MM / DD / YYYY<svg class="chev" width="13" height="13"><rect x="1" y="2" width="11" height="10" fill="none" stroke="#888"/><path d="M1 5h11M4 7h1M7 7h1M4 9h1M7 9h1" stroke="#888"/></svg></div>
  <div class="abs label" style="top:583px">Attach File:</div><div class="abs field" style="top:577px">Government Issues ID<svg class="chev" width="10" height="10"><path d="M1 3l4 4 4-4" fill="none" stroke="#555" stroke-width="1.3"/></svg></div>
  <div class="abs field" style="top:612px"><svg class="chev" width="14" height="14"><path d="M3 10l6-7a2 2 0 013 3l-6 7" fill="none" stroke="#999"/></svg></div>
  <div class="abs verify" style="top:614px"><span>✓</span>Verify</div>

  <div class="abs group" style="top:660px">Contact Information</div>
  <div class="abs label" style="top:698px">Phone:</div>
  <div class="abs field" style="top:692px;padding-left:62px">207 555 0143</div>
  <div class="abs" style="left:564px;top:693px;width:56px;height:24px;background:#ececec;border-right:1px solid #ccc;font-size:11px;padding:6px 5px"><span style="display:inline-block;width:14px;height:9px;background:#c9302c;vertical-align:-1px"></span>+44 ▾</div>
  <div class="abs verify" style="top:694px"><span>✓</span>Verify</div>
  <div class="abs label" style="top:734px">E-Mail:</div><div class="abs field hint" style="top:728px">sample@mailbox.example</div>
  <div class="abs verify" style="top:730px"><span>✓</span>Verify</div>

  <div class="abs group" style="top:775px">Residential Address</div>
  <div class="abs label" style="top:814px">Address line 1:</div><div class="abs field" style="top:808px"></div>
  <div class="abs label" style="top:850px">Address line 2:</div><div class="abs field" style="top:844px"></div>
  <div class="abs label" style="top:885px">Address line 3:</div><div class="abs field" style="top:879px"></div>
  <div class="abs label" style="top:921px">City:</div><div class="abs field" style="top:915px"></div>
  <div class="abs label" style="top:956px">Postcode:</div><div class="abs field" style="top:950px"></div>
  <div class="abs label" style="top:992px">Country:</div><div class="abs field" style="top:986px">United Kingdom<svg class="chev" width="10" height="10"><path d="M1 3l4 4 4-4" fill="none" stroke="#555" stroke-width="1.3"/></svg></div>
  <div class="abs label" style="top:1028px">Attach File:</div><div class="abs field hint" style="top:1022px">Utility Bill or Bank Statement<svg class="chev" width="14" height="14"><path d="M3 10l6-7a2 2 0 013 3l-6 7" fill="none" stroke="#999"/></svg></div>
  <div class="abs verify" style="top:1024px"><span>✓</span>Verify</div>

  <!-- footer -->
  <div class="abs footer">
    <div class="abs" style="left:98px;top:42px;width:130px;font-size:11px;letter-spacing:2px;line-height:17px;text-transform:uppercase">Northway Value Bureau</div>
    <div class="abs" style="left:228px;top:36px;width:1px;height:62px;background:rgba(255,255,255,.7)"></div>
    <div class="abs" style="left:240px;top:45px;width:12px;height:12px;border-radius:50%;background:#fff"></div>
    <div class="abs" style="left:98px;top:110px;font-size:9.5px;line-height:12.5px">© 2014 Northway Value Bureau.<br>All rights reserved</div>
    <h3 style="left:400px">ABOUT US</h3>
    <ul style="left:400px"><li>Rulebook</li><li>Trading Fees</li><li>Partners</li><li>Security</li><li>Terms of Service</li><li>Privacy Policy</li><li>Latest News</li></ul>
    <h3 style="left:628px">SUPPORT</h3>
    <ul style="left:628px"><li>What is Bitcoin?</li><li>How to buy a bitcoin?</li><li>How to sell a bitcoin?</li></ul>
    <h3 style="left:833px">FOLLOW NVB</h3>
    <div class="social" style="left:833px"></div>
    <div class="social" style="left:869px"></div>
    <div class="social" style="left:905px"></div>
    <div class="social" style="left:940px"></div>
    <div class="abs" role="img" aria-label="Hand-lettered slogan about changing the world one coin at a time" style="left:448px;top:185px;width:510px;height:68px;background:linear-gradient(90deg,rgba(255,255,255,.18),rgba(255,255,255,.28),rgba(255,255,255,.18));border-radius:6px"></div>
  </div>
</div>
</body>
</html>
```